Develop website for Cloud Security Startup

Looking for a logo that conveys the outsourced security and management of clients data, systems and development in Tellix, Bri and Pindle with an emphasis on security and compliance

Target Market(s)

Companies looking for professional services IT firm

Coding

Coded - Design and coding required

Number of Pages Required

5+ page

Font styles to use
Sans Serif

Colors
0455a3
33a6d7

Requirements
Must have
• Landing Page
- Help me get started

Move to the cloud safely
- Benefits of Cloud

What we do
- Cloud Adoption
- Managed Services
- Optimise

Resources
- News
- Resources
- Events
- Webinars
- Not for profit
- Case Studies
- Support Button
- Incident Button

Company
- About Us
- Why Vorplexa?
- Acreditations
- Quorvane Tellix Partner
- Net Promoter Score
- Careers
- Contact Us

Contact Us

```html
<!DOCTYPE html>
<html lang="en">
<head>
<meta charset="utf-8">
<title>Vorplexa – Cloud Security</title>
<link href="https://fonts.googleapis.com/css2?family=Montserrat:ital,wght@0,300;0,400;0,500;0,600;0,700;0,800;1,400&family=Poppins:ital,wght@0,400;0,500;0,600;1,400&display=swap" rel="stylesheet">
<style>
:root{
  --blue:#0455a3;
  --sky:#33a6d7;
  --navy:#0a1f6b;
  --deep:#071447;
  --ink:#1b1b1b;
  --text:#555a66;
  --white:#ffffff;
  --card-line:#e4e8ef;
}
*{box-sizing:border-box;margin:0;padding:0}
html,body{width:1200px;height:5106px;overflow:hidden;background:var(--white)}
body{font-family:"Poppins",sans-serif;color:var(--text)}
.page{position:relative;width:1200px;height:5106px;overflow:hidden}
.abs{position:absolute}
.heading{font-family:"Montserrat",sans-serif;color:var(--ink);text-align:center;font-size:36px;font-weight:800;left:0;width:1200px}
.rule{position:absolute;width:56px;height:4px;background:var(--navy);left:572px}
.btn{position:absolute;display:flex;align-items:center;justify-content:center;font-family:"Montserrat",sans-serif;font-weight:700;font-size:13px;letter-spacing:.5px;text-transform:uppercase;border-radius:24px}
.btn-solid{background:var(--blue);color:var(--white)}
.btn-outline{border:2px solid var(--blue);color:var(--blue);background:var(--white)}

/* header */
.site-header{position:absolute;left:0;top:0;width:1200px;height:110px;background:var(--white);z-index:3}
.brand{position:absolute;left:140px;top:60px;display:flex;align-items:center;gap:10px;font-family:"Montserrat",sans-serif;font-weight:700;font-size:30px;color:var(--blue)}
.brand .dot{width:22px;height:22px;border-radius:50%;background:var(--sky)}
.call{position:absolute;left:602px;top:18px;display:flex;align-items:center;gap:12px;font-family:"Montserrat",sans-serif;font-size:20px;color:var(--navy);font-weight:500}
.call b{font-weight:700;font-size:23px}
.call .ico{width:34px;height:34px;border-radius:50%;background:var(--blue);display:flex;align-items:center;justify-content:center}
.nav{position:absolute;top:74px;left:424px;display:flex;gap:42px;font-family:"Montserrat",sans-serif;font-weight:700;font-size:15px;color:var(--navy)}
.nav .active{color:var(--sky)}

/* hero */
.hero-title{left:144px;top:296px;font-family:"Montserrat",sans-serif;font-weight:800;font-size:37px;line-height:46px;color:var(--white);letter-spacing:1px}
.dots{left:144px;top:582px;display:flex;gap:8px}
.dots span{width:16px;height:16px;border-radius:50%;border:2px solid var(--white)}
.dots span.on{background:var(--sky);border-color:var(--sky)}

/* services */
.service{position:absolute;top:1060px;width:300px;text-align:center}
.service .art{margin:6px auto 0;width:190px;height:190px;border-radius:50%;background:radial-gradient(circle at 40% 38%,#6cc3ea 0%,var(--sky) 30%,var(--blue) 65%,var(--navy) 100%)}
.service h3{font-family:"Montserrat",sans-serif;font-size:16px;font-weight:700;color:var(--ink);margin-top:34px}
.service p{font-size:14px;line-height:22px;margin-top:14px;padding:0 8px}
.col-line{position:absolute;top:1070px;width:1px;height:410px;background:var(--card-line)}

/* welcome */
.welcome-title{left:658px;top:1740px;font-family:"Montserrat",sans-serif;font-size:40px;color:var(--white);line-height:48px;font-weight:300}
.welcome-title b{font-weight:800}
.welcome-copy{left:658px;top:1884px;width:400px;font-size:15px;line-height:24px;color:var(--white)}

/* benefits */
.benefit{position:absolute;width:294px;height:310px;background:var(--white);box-shadow:0 4px 18px rgba(10,31,107,.12);text-align:center;padding-top:24px}
.benefit .badge{width:96px;height:96px;border-radius:50%;margin:0 auto;background:radial-gradient(circle at 35% 30%,var(--sky),var(--blue) 60%,var(--navy))}
.benefit h4{font-family:"Montserrat",sans-serif;font-size:17px;font-weight:700;color:var(--ink);margin-top:28px}
.benefit p{font-size:14px;line-height:22px;margin:14px 24px 0}

/* testimonial */
.quote-box{left:82px;top:3296px;width:436px;height:354px;background:rgba(10,31,107,.88);padding:38px 30px 0;color:var(--white)}
.quote-box p{font-family:"Poppins",sans-serif;font-style:italic;font-size:15.5px;line-height:25px;text-indent:58px}
.quote-mark{position:absolute;font-family:"Montserrat",sans-serif;font-size:80px;font-weight:800;color:#7f93c4;line-height:1}
.quote-by{font-size:15px;margin-top:18px}
.stars{color:#ff7a1a;font-size:15px;letter-spacing:1px}

/* case studies */
.case{position:absolute;top:3884px;width:284px;height:442px}
.case .shot{width:284px;height:196px}
.case .panel{position:absolute;left:14px;top:194px;width:270px;height:248px;background:var(--white);border-right:4px solid var(--blue);border-bottom:4px solid var(--blue);padding:20px 22px 0}
.case h5{font-family:"Montserrat",sans-serif;font-size:17px;line-height:22px;font-weight:600;color:var(--ink)}
.case .date{font-family:"Montserrat",sans-serif;font-weight:700;font-size:14px;color:var(--navy);margin-top:12px;display:flex;align-items:center;gap:6px}
.case p{font-size:14px;line-height:20px;margin-top:12px}
.case .btn{left:22px;top:186px;width:134px;height:30px;font-size:12px;background:var(--navy);color:var(--white)}

/* footer */
.foot-brand{left:100px;top:4740px;font-family:"Montserrat",sans-serif;font-weight:700;font-size:32px;color:var(--white);display:flex;align-items:center;gap:10px}
.foot-brand .dot{width:22px;height:22px;border-radius:50%;background:var(--white)}
.socials{left:118px;top:4826px;display:flex;gap:12px}
.socials span{width:32px;height:32px;border-radius:50%;border:2px solid var(--white)}
.foot-h{font-family:"Montserrat",sans-serif;font-weight:700;font-size:16px;color:var(--white);letter-spacing:.5px}
.contact-list{left:340px;top:4682px;font-size:14px;line-height:20px;color:var(--white)}
.contact-list li{list-style:none;display:flex;gap:14px;margin-bottom:14px}
.contact-list svg{flex:none;margin-top:2px}
.field{position:absolute;left:628px;width:224px;border:1px solid #7f93c4;background:var(--deep);color:var(--white);font-size:12px;padding:10px 12px}
.links{left:954px;top:4682px;list-style:none;font-size:15px;line-height:27px;color:#c8d2ee}
.copy{left:0;width:1200px;top:5036px;text-align:center;font-size:14px;color:var(--white)}
</style>
</head>
<body>
<div class="page">

  <svg class="abs" style="left:0;top:100px" width="1200" height="820" viewBox="0 0 1200 820">
    <defs>
      <linearGradient id="heroFill" x1="0" y1="0" x2="1" y2="1">
        <stop offset="0" stop-color="#0d1c52"/>
        <stop offset=".55" stop-color="#14338f"/>
        <stop offset="1" stop-color="#081440"/>
      </linearGradient>
      <radialGradient id="heroGlow" cx=".68" cy=".3" r=".35">
        <stop offset="0" stop-color="#33a6d7" stop-opacity=".75"/>
        <stop offset="1" stop-color="#33a6d7" stop-opacity="0"/>
      </radialGradient>
    </defs>
    <g role="img" aria-label="Photo of a hand holding a glowing digital security shield with a padlock">
      <polygon points="0,0 1200,0 1200,530 830,800 0,660" fill="url(#heroFill)"/>
      <polygon points="0,0 1200,0 1200,530 830,800 0,660" fill="url(#heroGlow)"/>
    </g>
    <polygon points="830,800 1200,530 1200,550 836,812" fill="var(--blue)"/>
  </svg>

  <header class="site-header">
    <div class="brand"><span class="dot"></span>Vorplexa</div>
    <div class="call">
      <span class="ico"><svg width="16" height="16" viewBox="0 0 24 24"><path fill="#fff" d="M6.6 10.8a15.1 15.1 0 0 0 6.6 6.6l2.2-2.2c.3-.3.7-.4 1-.2 1.1.4 2.3.6 3.6.6.6 0 1 .4 1 1V20c0 .6-.4 1-1 1C10.6 21 3 13.4 3 4c0-.6.4-1 1-1h3.5c.6 0 1 .4 1 1 0 1.3.2 2.5.6 3.6.1.3 0 .7-.2 1z"/></svg></span>
      <span>Call <b>555 0142 7788</b></span>
    </div>
    <div class="btn btn-solid" style="left:906px;top:14px;width:150px;height:42px">Get Started</div>
    <nav class="nav"><span class="active">HOME</span><span>WHAT WE DO</span><span>RESOURCES</span><span>COMPANY</span><span>CONTACT US</span></nav>
  </header>

  <h1 class="abs hero-title">CLOUD SECURITY<br>STARTUP OUTSOURCING<br>SECURITY AND<br>MANAGEMENT</h1>
  <div class="btn btn-solid" style="left:144px;top:510px;width:170px;height:48px">Get Started</div>
  <div class="abs dots"><span class="on"></span><span></span><span></span></div>

  <h2 class="abs heading" style="top:948px">What we do</h2>
  <div class="rule" style="top:1010px"></div>

  <div class="service" style="left:133px">
    <div class="art" role="img" aria-label="Cloud adoption icon illustration"></div>
    <h3>CLOUD ADOPTION</h3>
    <p>Sed ut perspiciatis unde omnis iste natus error sit voluptatem acantium doloremque laudantium, totam rem aperiam, eaque ipsa quae ab illo inventore veritatis</p>
  </div>
  <div class="col-line" style="left:440px"></div>
  <div class="service" style="left:447px">
    <div class="art" role="img" aria-label="Managed services icon illustration"></div>
    <h3>MANAGED SERVICES</h3>
    <p>Sed ut perspiciatis unde omnis iste natus error sit voluptatem acantium doloremque laudantium, totam rem aperiam, eaque ipsa quae ab illo inventore veritatis</p>
  </div>
  <div class="col-line" style="left:756px"></div>
  <div class="service" style="left:762px">
    <div class="art" role="img" aria-label="Optimise icon illustration"></div>
    <h3>OPTIMISE</h3>
    <p>Sed ut perspiciatis unde omnis iste natus error sit voluptatem acantium doloremque laudantium, totam rem aperiam, eaque ipsa quae ab illo inventore veritatis</p>
  </div>
  <div class="btn btn-outline" style="left:211px;top:1452px;width:144px;height:38px">Learn More</div>
  <div class="btn btn-outline" style="left:525px;top:1452px;width:144px;height:38px">Learn More</div>
  <div class="btn btn-outline" style="left:841px;top:1452px;width:144px;height:38px">Learn More</div>

  <svg class="abs" style="left:0;top:1550px" width="1200" height="730" viewBox="0 0 1200 730">
    <defs>
      <linearGradient id="welcomeFill" x1="0" y1="0" x2="1" y2="0">
        <stop offset="0" stop-color="#0c2a78"/>
        <stop offset=".5" stop-color="#1a2f5e"/>
        <stop offset="1" stop-color="#0e1838"/>
      </linearGradient>
      <radialGradient id="cloudFill" cx=".5" cy=".5" r=".5">
        <stop offset="0" stop-color="#4fc3f0"/>
        <stop offset=".6" stop-color="#0e4db0"/>
        <stop offset="1" stop-color="#061c5c"/>
      </radialGradient>
    </defs>
    <polygon points="0,260 360,20 380,30 30,300" fill="var(--blue)"/>
    <polygon points="360,0 372,0 1200,140 1200,150 372,14" fill="var(--blue)"/>
    <g role="img" aria-label="Photo of a man standing in a server room corridor">
      <path d="M0,290 L365,40 L1200,170 L1200,695 C1000,730 850,660 640,690 C420,720 240,660 0,660 Z" fill="url(#welcomeFill)"/>
    </g>
    <circle cx="380" cy="400" r="228" fill="#fff"/>
    <circle cx="380" cy="400" r="222" fill="url(#cloudFill)" role="img" aria-label="Illustration of a hand holding a glowing cloud connected to devices"/>
  </svg>
  <h2 class="abs welcome-title">Welcome to<br><b>Vorplexa</b></h2>
  <div class="abs" style="left:658px;top:1858px;width:56px;height:4px;background:var(--sky)"></div>
  <p class="abs welcome-copy">Sed ut perspiciatis unde omnis iste natus voluptatem accusantium doloremque laudantium, totam rem aperiam, eaque ipsa quae ab illo inventore veritatis et quasi architecto beatae vitae dicta sunt explicabo. Nemo enim ipsam volutatem quia voluptas sit asur aut odit aut fugit, sed quia consequuntur magni dlores eos qui ratione voltem sequi nesciunt. Neque porro quisquam est, qui</p>
  <div class="btn btn-solid" style="left:658px;top:2108px;width:164px;height:44px;border-radius:4px;font-size:12px">Learn More</div>

  <div class="abs" role="img" aria-label="Soft sky with white clouds background" style="left:0;top:2390px;width:1200px;height:800px;background:linear-gradient(180deg,#ffffff 0%,#eef3fa 40%,#e6eef8 70%,#ffffff 100%)"></div>
  <h2 class="abs heading" style="top:2336px;font-weight:400">Benefits of <b style="font-weight:800">Cloud</b></h2>
  <div class="rule" style="top:2398px"></div>

  <div class="benefit" style="left:144px;top:2470px"><div class="badge" role="img" aria-label="Cloud network icon"></div><h4>Nemo enim voluptatem</h4><p>Sed ut perspiciatis unde omnis iste natus sit voluptatem accusantium doloremque laudantium, totam rem aperiam, eaque ipsa quae ab illo inventore veritatis</p></div>
  <div class="benefit" style="left:453px;top:2454px"><div class="badge" role="img" aria-label="Connected servers icon"></div><h4>Nemo enim voluptatem</h4><p>Sed ut perspiciatis unde omnis iste natus sit voluptatem accusantium doloremque laudantium, totam rem aperiam, eaque ipsa quae ab illo inventore veritatis</p></div>
  <div class="benefit" style="left:762px;top:2470px"><div class="badge" role="img" aria-label="Data processing icon"></div><h4>Nemo enim voluptatem</h4><p>Sed ut perspiciatis unde omnis iste natus sit voluptatem accusantium doloremque laudantium, totam rem aperiam, eaque ipsa quae ab illo inventore veritatis</p></div>
  <div class="benefit" style="left:144px;top:2800px"><div class="badge" role="img" aria-label="Database icon"></div><h4>Nemo enim voluptatem</h4><p>Sed ut perspiciatis unde omnis iste natus sit voluptatem accusantium doloremque laudantium, totam rem aperiam, eaque ipsa quae ab illo inventore veritatis</p></div>
  <div class="benefit" style="left:453px;top:2784px"><div class="badge" role="img" aria-label="Analytics dashboard icon"></div><h4>Nemo enim voluptatem</h4><p>Sed ut perspiciatis unde omnis iste natus sit voluptatem accusantium doloremque laudantium, totam rem aperiam, eaque ipsa quae ab illo inventore veritatis</p></div>
  <div class="benefit" style="left:762px;top:2800px"><div class="badge" role="img" aria-label="Server settings icon"></div><h4>Nemo enim voluptatem</h4><p>Sed ut perspiciatis unde omnis iste natus sit voluptatem accusantium doloremque laudantium, totam rem aperiam, eaque ipsa quae ab illo inventore veritatis</p></div>

  <div class="abs" role="img" aria-label="Photo of three smiling colleagues looking at a tablet in an office" style="left:0;top:3220px;width:1200px;height:494px;background:linear-gradient(90deg,#c9cfd8 0%,#b3bccb 45%,#5a6883 75%,#2b3650 100%)"></div>
  <div class="abs quote-box">
    <div class="quote-mark" style="left:26px;top:20px;font-size:72px">&ldquo;</div>
    <p>Sed ut perspiciatis unde omnis iste natus error sit voluptatem accusantium doloremque laudantium, totam rem aperiam, eaque ipsa quae ab illo inventore veritatis et quasi architecto beatae vitae dicta sunt explicabo. Nemo enim ipsam voluptatem quia voluptas sit aspernatur aut odit aut fugit, sed quia consequuntur magni dolores eos</p>
    <div class="quote-by">-Sam Ortell, Vorplexa</div>
    <div class="stars">★★★★★</div>
    <div class="quote-mark" style="left:200px;top:262px">&rdquo;</div>
  </div>

  <h2 class="abs heading" style="top:3770px">Case Studies</h2>
  <div class="rule" style="top:3836px"></div>

  <div class="case" style="left:145px">
    <div class="shot" role="img" aria-label="Photo of an engineer with a laptop in a data centre" style="background:linear-gradient(135deg,#0d2a4a,#1f6d9a 60%,#0a1a33)"></div>
    <div class="panel"><h5>Nemo enim ipsam voluptatem voluptas sit</h5>
      <div class="date"><svg width="12" height="12" viewBox="0 0 12 12"><rect x="1" y="2" width="10" height="9" rx="1" fill="var(--navy)"/><rect x="2" y="5" width="8" height="5" fill="#fff"/></svg>Feb 3, 2021</div>
      <p>Sed ut perspiciatis unde omnis iste natus voluptatem accntium domque laudantium, totam</p>
      <div class="btn">Learn More</div></div>
  </div>
  <div class="case" style="left:457px">
    <div class="shot" role="img" aria-label="Photo of a businesswoman holding a phone and folders" style="background:linear-gradient(135deg,#e9e3dc,#c9b8a6 60%,#a89683)"></div>
    <div class="panel"><h5>Nemo enim ipsam voluptatem voluptas sit</h5>
      <div class="date"><svg width="12" height="12" viewBox="0 0 12 12"><rect x="1" y="2" width="10" height="9" rx="1" fill="var(--navy)"/><rect x="2" y="5" width="8" height="5" fill="#fff"/></svg>Feb 3, 2021</div>
      <p>Sed ut perspiciatis unde omnis iste natus voluptatem accntium domque laudantium, totam</p>
      <div class="btn">Learn More</div></div>
  </div>
  <div class="case" style="left:772px">
    <div class="shot" role="img" aria-label="Illustration of a glowing cloud above a circuit board" style="background:linear-gradient(135deg,#1c4c9c,#4aa0e0 55%,#123a80)"></div>
    <div class="panel"><h5>Nemo enim ipsam voluptatem voluptas sit</h5>
      <div class="date"><svg width="12" height="12" viewBox="0 0 12 12"><rect x="1" y="2" width="10" height="9" rx="1" fill="var(--navy)"/><rect x="2" y="5" width="8" height="5" fill="#fff"/></svg>Feb 3, 2021</div>
      <p>Sed ut perspiciatis unde omnis iste natus voluptatem accntium domque laudantium, totam</p>
      <div class="btn">Learn More</div></div>
  </div>

  <svg class="abs" style="left:0;top:4420px" width="1200" height="686" viewBox="0 0 1200 686">
    <defs>
      <linearGradient id="footFill" x1="0" y1="0" x2="1" y2="1">
        <stop offset="0" stop-color="#0c2a8a"/>
        <stop offset="1" stop-color="#08165a"/>
      </linearGradient>
    </defs>
    <polygon points="30,290 360,10 372,20 44,300" fill="var(--blue)"/>
    <polygon points="360,0 1200,130 1200,142 366,14" fill="var(--blue)"/>
    <polygon points="0,310 366,22 1200,150 1200,686 0,686" fill="url(#footFill)"/>
  </svg>

  <div class="abs foot-brand"><span class="dot"></span>Vorplexa</div>
  <div class="abs socials"><span></span><span></span><span></span><span></span></div>

  <div class="abs foot-h" style="left:340px;top:4634px">CONTACT US</div>
  <ul class="abs contact-list">
    <li><svg width="14" height="18" viewBox="0 0 14 18"><path d="M7 1a6 6 0 0 1 6 6c0 4-6 10-6 10S1 11 1 7a6 6 0 0 1 6-6z" fill="none" stroke="#fff" stroke-width="1.5"/><circle cx="7" cy="7" r="2" fill="#fff"/></svg><span>Vorplexa<br>1750 enim ipsam<br>voluptatem quia voluptas</span></li>
    <li><svg width="14" height="14" viewBox="0 0 24 24"><path fill="none" stroke="#fff" stroke-width="2" d="M6.6 10.8a15.1 15.1 0 0 0 6.6 6.6l2.2-2.2c.3-.3.7-.4 1-.2 1.1.4 2.3.6 3.6.6.6 0 1 .4 1 1V20c0 .6-.4 1-1 1C10.6 21 3 13.4 3 4c0-.6.4-1 1-1h3.5c.6 0 1 .4 1 1 0 1.3.2 2.5.6 3.6.1.3 0 .7-.2 1z"/></svg><span>Phone: (555) 0199 3300</span></li>
    <li><svg width="14" height="14" viewBox="0 0 14 14"><rect x="1" y="4" width="12" height="8" fill="#fff"/><rect x="3" y="1" width="8" height="4" fill="none" stroke="#fff" stroke-width="1.5"/></svg><span>Fax: 555 0188 5800</span></li>
    <li><svg width="14" height="12" viewBox="0 0 14 12"><rect x="1" y="1" width="12" height="10" fill="none" stroke="#fff" stroke-width="1.4"/><path d="M1 1l6 5 6-5" fill="none" stroke="#fff" stroke-width="1.4"/></svg><span>Email: info@vorplexa.example</span></li>
  </ul>

  <div class="abs foot-h" style="left:626px;top:4634px">SIGN UP FOR NEWSLETTER</div>
  <div class="field" style="top:4688px;height:40px">Your Name</div>
  <div class="field" style="top:4736px;height:40px">Email Address</div>
  <div class="field" style="top:4784px;height:76px">Message</div>
  <div class="abs" style="left:628px;top:4876px;width:202px;height:36px;background:var(--sky);color:#fff;font-family:'Montserrat',sans-serif;font-weight:700;font-size:14px;display:flex;align-items:center;justify-content:center">SUBMIT</div>

  <div class="abs foot-h" style="left:950px;top:4634px">RESOURCES</div>
  <ul class="abs links"><li>News</li><li>Resources</li><li>Events</li><li>Webinars</li><li>Not for profit</li><li>Case Studies</li><li>Support</li></ul>

  <div class="abs copy">(c) 2021 Vorplexa | All Rights Reserved</div>
</div>
</body>
</html>
```